Card Design for my dog training business Brightpaw Obedience

Need a business card design for my dog training business with my new logo. Want the card to come off professional yet fun. Want it to be very eye catchy as well. I normally have these at vet clinics, pet stores, and groomers. so need it to look better than my competitors.
Target Market(s)
dog owners
Industry/Entity Type
Dog Training
Contact Information for Business Card
needs logo, my name and info
Font styles to use
Serif
Colors
0255a3
ffffff
ec1f27
000000
333333
fbfbfb
Requirements
Must have
- Brightpaw Obedience
- Felix Orland
- 415 903 2276
- info@brightpawobedience.example
- www.brightpawobedience.example

```html
<!DOCTYPE html>
<html lang="en">
<head>
<meta charset="utf-8">
<title>Brightpaw Obedience – Business Card</title>
<link rel="stylesheet" href="https://fonts.googleapis.com/css2?family=Tinos&family=Lato:wght@400&display=swap">
<style>
  :root {
    --page-bg: #e8e8e8;
    --card-bg: #383838;
    --ink-light: #ffffff;
    --ink-dark: #000000;
    --disc-light: #fbfbfb;
    --disc-shade: #d6d6d6;
  }
  * { margin: 0; padding: 0; box-sizing: border-box; }
  html, body {
    width: 1200px;
    height: 900px;
    overflow: hidden;
    background: var(--page-bg);
  }
  .business-card {
    position: absolute;
    left: 150px;
    top: 170px;
    width: 900px;
    height: 560px;
    background: var(--card-bg);
    box-shadow: 0 10px 30px rgba(0,0,0,0.25);
    overflow: hidden;
  }
  .holder-name {
    position: absolute;
    left: 48px;
    top: 92px;
    font-family: "Tinos", "Times New Roman", serif;
    font-size: 30px;
    letter-spacing: 0.5px;
    color: var(--ink-light);
    text-transform: uppercase;
  }
  .contact-list {
    position: absolute;
    left: 48px;
    top: 364px;
    list-style: none;
    font-family: "Lato", Arial, sans-serif;
    font-size: 21px;
    color: var(--ink-light);
  }
  .contact-list li {
    display: flex;
    align-items: center;
    height: 33px;
  }
  .contact-icon {
    width: 18px;
    height: 18px;
    margin-right: 10px;
    fill: var(--ink-light);
    flex: none;
  }
  .brand-disc {
    position: absolute;
    left: 367px;
    top: 25px;
    width: 506px;
    height: 506px;
    border-radius: 50%;
    background: radial-gradient(circle at 45% 40%, var(--disc-light) 0%, #eeeeee 55%, var(--disc-shade) 100%);
    box-shadow: 0 0 0 3px rgba(255,255,255,0.35);
    display: flex;
    align-items: center;
    justify-content: center;
  }
  .brand-name {
    font-family: "Tinos", "Times New Roman", serif;
    font-size: 50px;
    line-height: 1.1;
    color: var(--ink-dark);
    text-align: center;
  }
</style>
</head>
<body>
  <div class="business-card">
    <p class="holder-name">Felix Orland</p>

    <ul class="contact-list">
      <li>
        <svg class="contact-icon" viewBox="0 0 24 24" aria-hidden="true"><path d="M6.6 10.8a15.1 15.1 0 0 0 6.6 6.6l2.2-2.2a1 1 0 0 1 1-.25 11.4 11.4 0 0 0 3.6.57 1 1 0 0 1 1 1V20a1 1 0 0 1-1 1A17 17 0 0 1 3 4a1 1 0 0 1 1-1h3.5a1 1 0 0 1 1 1c0 1.25.2 2.45.57 3.57a1 1 0 0 1-.25 1z"/></svg>
        415 903 2276
      </li>
      <li>
        <svg class="contact-icon" viewBox="0 0 24 24" aria-hidden="true"><path d="M2 5h20v14H2z M4 7v.4l8 5 8-5V7l-8 5z" fill-rule="evenodd"/></svg>
        info@brightpawobedience.example
      </li>
      <li>
        <svg class="contact-icon" viewBox="0 0 24 24" aria-hidden="true"><circle cx="12" cy="12" r="10"/><path d="M2 12h20M12 2c3 3 3 17 0 20M12 2c-3 3-3 17 0 20" stroke="#383838" stroke-width="1.5" fill="none"/></svg>
        www.brightpawobedience.example
      </li>
    </ul>

    <div class="brand-disc">
      <p class="brand-name">Brightpaw<br>Obedience</p>
    </div>
  </div>
</body>
</html>
```